Business card design needed

I am looking for a simple but elegant business card that has a professional and a classy look and feel about it. Must engage the persons attention.
I own and run multiple dental practices and offer basic to advanced dentistry.

Target Market(s)

people looking for dentists

Industry/Entity Type

Dental

Contact Information for Business Card

Dr. Desmond Falkner
Bellwood Dental
gentle care every visit
Tallowbrook - 14 Tarvin Street Ph: 0741586297
Fernhollow - 52 Hollis Street Ph: 0741369014
Quillby - Shop 8 27 Corbett Drive Ph: 41628473
Email: df@bellwooddental.com.au

Requirements
Must have
• Contact Details
QR codes for easy storage and website redirection
email and web address

```html
<!DOCTYPE html>
<html lang="en">
<head>
<meta charset="utf-8">
<title>Bellwood Dental – Business Card</title>
<link rel="stylesheet" href="https://fonts.googleapis.com/css2?family=Hind:wght@300;400;500&family=Tinos&display=swap">
<style>
  :root {
    --stage: #737575;
    --paper-light: #fafafa;
    --paper: #dedfe1;
    --blue-light: #3cb0e5;
    --blue: #1a8ecd;
    --blue-deep: #1577b3;
    --ink: #5b5c5e;
    --white: #ffffff;
    --sans: "Hind", Arial, sans-serif;
    --serif: "Tinos", "Times New Roman", serif;
  }
  * { margin: 0; padding: 0; box-sizing: border-box; }
  html, body { width: 1200px; height: 1014px; overflow: hidden; }
  body { background: var(--stage); position: relative; }

  .card {
    position: absolute;
    left: 413px;
    width: 506px;
    height: 339px;
    border-radius: 28px;
    overflow: hidden;
  }
  .card--front { top: 96px; }
  .card--back { top: 516px; }
  .card__art { position: absolute; inset: 0; width: 100%; height: 100%; }

  .front__brand {
    position: absolute; left: 0; right: 0; top: 152px;
    text-align: center; color: var(--white);
  }
  .front__name {
    font-family: var(--sans); font-weight: 400;
    font-size: 46px; letter-spacing: 2px; line-height: 1;
  }
  .front__tagline {
    font-family: var(--serif); font-size: 35px; line-height: 1; margin-top: 4px;
  }

  .back__brand { position: absolute; left: 30px; top: 30px; color: var(--ink); }
  .back__name {
    font-family: var(--sans); font-size: 23px; letter-spacing: 1.5px; line-height: 1;
  }
  .back__tagline { font-family: var(--serif); font-size: 14px; line-height: 1; margin-top: 1px; }

  .back__email {
    position: absolute; right: 20px; top: 28px;
    font-family: var(--sans); font-size: 11px; color: var(--ink);
    display: flex; align-items: center; gap: 7px;
  }
  .back__email svg { width: 13px; height: 9px; }

  .back__doctor {
    position: absolute; left: 0; right: 0; top: 110px;
    text-align: center; font-family: var(--serif); font-size: 33px;
    color: var(--ink); line-height: 1;
  }

  .practice {
    position: absolute; top: 256px;
    font-family: var(--sans); font-weight: 500; font-size: 11px;
    color: var(--white); line-height: 13px;
  }
  .practice--tallowbrook { left: 41px; }
  .practice--fernhollow { left: 206px; }
  .practice--quillby { left: 343px; }
  .practice__row { display: flex; gap: 8px; align-items: flex-start; }
  .practice__row + .practice__row { margin-top: 8px; }
  .practice svg { width: 12px; height: 11px; flex: none; margin-top: 1px; }
</style>
</head>
<body>

<svg width="0" height="0" style="position:absolute" aria-hidden="true">
  <defs>
    <radialGradient id="paperGlow" cx="0.5" cy="0.4" r="0.6">
      <stop offset="0" stop-color="#fafafa"/>
      <stop offset="1" stop-color="#dedfe1"/>
    </radialGradient>
    <linearGradient id="blueBand" x1="0" y1="0" x2="1" y2="1">
      <stop offset="0" stop-color="#3cb0e5"/>
      <stop offset="1" stop-color="#1a8ecd"/>
    </linearGradient>
  </defs>
  <symbol id="icon-home" viewBox="0 0 12 11"><path d="M6 0 L12 5.5 L10.5 5.5 L10.5 11 L7.5 11 L7.5 7.5 L4.5 7.5 L4.5 11 L1.5 11 L1.5 5.5 L0 5.5 Z" fill="#fff"/></symbol>
  <symbol id="icon-phone" viewBox="0 0 12 11"><path d="M2.2 0.3 L4 2.4 L3 3.7 C3.8 5.5 5.3 7 7.3 7.9 L8.6 6.8 L11 8.5 L9.8 10.6 C5 10.2 1.2 6.2 0.6 1.6 Z" fill="#fff"/></symbol>
</svg>

<section class="card card--front" aria-label="Card front">
  <svg class="card__art" viewBox="0 0 549 368" preserveAspectRatio="none" aria-hidden="true">
    <rect width="549" height="368" fill="url(#paperGlow)"/>
    <path d="M0 96 L549 124 L549 368 L0 368 Z" fill="url(#blueBand)"/>
    <path d="M0 90 L549 118" stroke="var(--blue-deep)" stroke-width="2"/>
  </svg>
  <div class="front__brand">
    <div class="front__name">Bellwood Dental</div>
    <div class="front__tagline">gentle care every visit</div>
  </div>
</section>

<section class="card card--back" aria-label="Card back">
  <svg class="card__art" viewBox="0 0 549 368" preserveAspectRatio="none" aria-hidden="true">
    <rect width="549" height="368" fill="url(#paperGlow)"/>
    <path d="M0 232 L549 260 L549 368 L0 368 Z" fill="url(#blueBand)"/>
    <path d="M0 226 L549 254" stroke="var(--blue-deep)" stroke-width="2"/>
  </svg>

  <div class="back__brand">
    <div class="back__name">Bellwood Dental</div>
    <div class="back__tagline">gentle care every visit</div>
  </div>

  <div class="back__email">
    <svg viewBox="0 0 13 9" aria-hidden="true"><rect x="0.5" y="0.5" width="12" height="8" fill="none" stroke="var(--ink)"/><path d="M0.5 0.5 L6.5 5 L12.5 0.5" fill="none" stroke="var(--ink)"/></svg>
    <span>df@bellwooddental.com.au</span>
  </div>

  <div class="back__doctor">Dr. Desmond Falkner</div>

  <div class="practice practice--tallowbrook">
    <div class="practice__row"><svg><use href="#icon-home"/></svg><span>Tallowbrook<br>14 Tarvin Street</span></div>
    <div class="practice__row"><svg><use href="#icon-phone"/></svg><span>0741586297</span></div>
  </div>
  <div class="practice practice--fernhollow">
    <div class="practice__row"><svg><use href="#icon-home"/></svg><span>Fernhollow<br>52 Hollis Street</span></div>
    <div class="practice__row"><svg><use href="#icon-phone"/></svg><span>0741369014</span></div>
  </div>
  <div class="practice practice--quillby">
    <div class="practice__row"><svg><use href="#icon-home"/></svg><span>Quillby<br>Shop 8 27 Corbett Drive</span></div>
    <div class="practice__row"><svg><use href="#icon-phone"/></svg><span>41628473</span></div>
  </div>
</section>

</body>
</html>
```